Roofing Company Modern look

I want a modern and sophisticated look for our roofing business.

Our address is :

5217 Mallow Creek Ln
Orlando, Fl 32825

(407)-583-2196

www.HarborlineRoofsFl.com

I also want to make sure on the back there is a spot to put
Project Manager Name :

Number:

Because the cards will be used by all sales people

Project Manager Name :

Also there are accreditation we have logos are uploaded here as well that I would like maybe on the back of card as well

I also want to highlight our special attributions or trades:

Residential & Commercial
Fully Insured
License # CCC7482913
Insurance Claims
Serving Central Florida Since 1992
Free Estimates

Contact Information for Business Card

Our address is :

5217 Mallow Creek Ln
Orlando, Fl 32825

(407)-583-2196

Project Manager Name :

Residential & Commercial
Fully Insured
License # CCC7482913
Insurance Claims
Free Estimates

Font styles to use
Serif
Sans Serif

Colors
3176b5

Requirements
Must have
• Must have royal blue like my logo grey and black are the colors I like

```html
<!DOCTYPE html>
<html lang="en">
<head>
<meta charset="utf-8">
<title>Harborline Roofing &amp; Gutters — Business Card</title>
<link href="https://fonts.googleapis.com/css2?family=Nunito+Sans:wght@400;800&family=Questrial&family=Roboto+Condensed:wght@400;500&display=swap" rel="stylesheet">
<style>
  :root {
    --royal-blue: #1a7cc4;
    --cyan: #1fb2e4;
    --cyan-dark: #1498c9;
    --charcoal: #2e2e30;
    --grey-text: #3a3a3a;
    --page: #e4e4e4;
    --card: #ffffff;
    --badge-fill: #dde1e6;
  }
  * { box-sizing: border-box; margin: 0; padding: 0; }
  html, body { width: 1200px; height: 1200px; overflow: hidden; }
  body { background: var(--page); position: relative; font-family: "Questrial", sans-serif; }

  .card {
    position: absolute; left: 262px; width: 686px; height: 392px;
    background: var(--card); border-radius: 22px; overflow: hidden;
  }
  .card--front { top: 165px; }
  .card--back { top: 653px; }

  .edge-band { position: absolute; left: 0; right: 0; bottom: 0; height: 11px; display: flex; gap: 4px; }
  .edge-band__blue { width: 340px; background: var(--royal-blue); }
  .edge-band__dark { flex: 1; background: var(--charcoal); }

  /* Front */
  .phone-tab {
    position: absolute; left: 387px; top: 21px; width: 299px; height: 53px;
    background: linear-gradient(180deg, var(--cyan), var(--cyan-dark));
    border-radius: 27px 0 0 27px; display: flex; align-items: center; gap: 8px; padding-left: 16px;
    color: #fff; font-family: "Nunito Sans", sans-serif; font-weight: 800; font-size: 30px;
  }
  .phone-tab svg { width: 32px; height: 32px; flex: none; }

  .brand-mark {
    position: absolute; left: 303px; top: 125px; width: 80px; height: 80px;
    border-radius: 50%; background: var(--royal-blue);
  }
  .brand-name {
    position: absolute; left: 0; right: 0; top: 220px; text-align: center;
    color: var(--grey-text); font-family: "Questrial", sans-serif; font-weight: 400;
  }
  .brand-name__main { display: block; font-size: 38px; letter-spacing: 3px; line-height: 1; }
  .brand-name__sub { display: block; font-size: 13px; letter-spacing: 2.5px; margin-top: 6px; }

  .address {
    position: absolute; left: 163px; width: 358px; top: 299px; text-align: center;
    font-size: 17px; color: var(--grey-text); padding-bottom: 4px;
    border-bottom: 2px solid var(--royal-blue); white-space: nowrap;
  }
  .website {
    position: absolute; left: 0; right: 0; top: 330px; text-align: center;
    font-size: 17px; color: var(--grey-text); letter-spacing: 0.3px;
  }
  .website strong { color: var(--royal-blue); font-family: "Nunito Sans", sans-serif; font-weight: 800; }

  /* Back */
  .field {
    position: absolute; left: 59px; width: 561px; display: flex; align-items: flex-end;
    font-family: "Roboto Condensed", sans-serif; font-weight: 500; font-size: 15px; color: var(--royal-blue);
  }
  .field__line { flex: 1; border-bottom: 1px solid var(--royal-blue); margin-left: 4px; margin-bottom: 3px; }
  .field--manager { top: 62px; }
  .field--phone { top: 116px; }

  .services { position: absolute; top: 170px; list-style: none; font-family: "Roboto Condensed", sans-serif; font-weight: 500; font-size: 18px; color: var(--royal-blue); }
  .services--left { left: 59px; }
  .services--right { left: 335px; }
  .services li { display: flex; align-items: center; gap: 10px; height: 22px; }
  .services svg { width: 19px; height: 19px; flex: none; }

  .badge { position: absolute; top: 277px; height: 60px; background: var(--badge-fill); border-radius: 8px; }
  .badge--a { left: 61px; width: 48px; }
  .badge--b { left: 191px; width: 68px; }
  .badge--c { left: 335px; width: 144px; top: 285px; height: 44px; }
  .badge--d { left: 566px; width: 60px; border-radius: 50%; }
</style>
</head>
<body>

<section class="card card--front">
  <div class="phone-tab">
    <svg viewBox="0 0 32 32" aria-hidden="true">
      <circle cx="16" cy="16" r="15" fill="#fff"/>
      <path d="M11 8.5c.8-.6 1.8-.4 2.3.4l1.6 2.6c.4.7.3 1.6-.3 2.1l-1.2 1c.8 1.8 2.1 3.2 3.9 4.1l1-1.2c.5-.6 1.4-.8 2.1-.3l2.6 1.6c.8.5 1 1.6.4 2.3l-1.1 1.4c-.8 1-2.200 1.3-3.4.8-4.1-1.8-7.2-5-8.9-9.1-.5-1.2-.1-2.6.9-3.3z" fill="var(--cyan-dark)"/>
    </svg>
    <span>(407)-583-2196</span>
  </div>

  <div class="brand-mark" aria-hidden="true"></div>
  <h1 class="brand-name">
    <span class="brand-name__main">HARBORLINE</span>
    <span class="brand-name__sub">ROOFING &amp; GUTTERS INC.</span>
  </h1>

  <p class="address">5217 MALLOW CREEK LN, ORLANDO, FL 32825</p>
  <p class="website">WWW.<strong>HARBORLINE</strong>ROOFSFL.COM</p>

  <div class="edge-band"><span class="edge-band__blue"></span><span class="edge-band__dark"></span></div>
</section>

<section class="card card--back">
  <div class="field field--manager"><span>PROJECT MANAGER NAME :</span><span class="field__line"></span></div>
  <div class="field field--phone"><span>PHONE:</span><span class="field__line"></span></div>

  <ul class="services services--left">
    <li><svg viewBox="0 0 20 20" aria-hidden="true"><path d="M3 10.5l4.5 4.5L17 5" fill="none" stroke="var(--royal-blue)" stroke-width="2.6" stroke-linecap="round" stroke-linejoin="round"/></svg>Residential &amp; Commercial</li>
    <li><svg viewBox="0 0 20 20" aria-hidden="true"><path d="M3 10.5l4.5 4.5L17 5" fill="none" stroke="var(--royal-blue)" stroke-width="2.6" stroke-linecap="round" stroke-linejoin="round"/></svg>Fully Insured</li>
    <li><svg viewBox="0 0 20 20" aria-hidden="true"><path d="M3 10.5l4.5 4.5L17 5" fill="none" stroke="var(--royal-blue)" stroke-width="2.6" stroke-linecap="round" stroke-linejoin="round"/></svg>License # CCC7482913</li>
  </ul>
  <ul class="services services--right">
    <li><svg viewBox="0 0 20 20" aria-hidden="true"><path d="M3 10.5l4.5 4.5L17 5" fill="none" stroke="var(--royal-blue)" stroke-width="2.6" stroke-linecap="round" stroke-linejoin="round"/></svg>Insurance Claims</li>
    <li><svg viewBox="0 0 20 20" aria-hidden="true"><path d="M3 10.5l4.5 4.5L17 5" fill="none" stroke="var(--royal-blue)" stroke-width="2.6" stroke-linecap="round" stroke-linejoin="round"/></svg>Serving Central Florida Since 1992</li>
    <li><svg viewBox="0 0 20 20" aria-hidden="true"><path d="M3 10.5l4.5 4.5L17 5" fill="none" stroke="var(--royal-blue)" stroke-width="2.6" stroke-linecap="round" stroke-linejoin="round"/></svg>Free Estimates</li>
  </ul>

  <div class="badge badge--a" role="img" aria-label="Business accreditation badge"></div>
  <div class="badge badge--b" role="img" aria-label="Shingle applicator certification badge"></div>
  <div class="badge badge--c" role="img" aria-label="Authorized roofing contractor badge"></div>
  <div class="badge badge--d" role="img" aria-label="Screened and approved listing badge"></div>

  <div class="edge-band"><span class="edge-band__blue"></span><span class="edge-band__dark"></span></div>
</section>

</body>
</html>
```